Need Business Card for our Real Estate Business with Sales Executive's Picture

PANTONE 484 C ( RED)

PANTONE 2766 C ( BLUE

Industry/Entity Type

Real Estate

Contact Information for Business Card

Name, Mobile, email, & picture of Person
Agency Phone, address, Web address

Requirements
Must have
• Our Logo Colours, Agent Picture,

```html
<!DOCTYPE html>
<html lang="en">
<head>
<meta charset="utf-8">
<title>Dunmore Realty – Business Card</title>
<link href="https://fonts.googleapis.com/css2?family=Open+Sans:wght@400;600;700&display=swap" rel="stylesheet">
<style>
  :root{
    --bg:#3a3a3b;
    --card:#2a2a2b;
    --card-edge:#232324;
    --red:#a8282a;
    --white:#f4f4f4;
    --muted:#5a5a5c;
    --photo-a:#2f4f9c;
    --photo-b:#c49a82;
  }
  *{box-sizing:border-box;margin:0;padding:0}
  html,body{width:799px;height:1200px;overflow:hidden}
  body{background:var(--bg);font-family:"Open Sans",sans-serif;color:var(--white);position:relative}
  .card{position:absolute;left:84px;width:630px;height:360px;background:var(--card);border:1px solid var(--card-edge);border-radius:3px;overflow:hidden;box-shadow:0 12px 30px rgba(0,0,0,.45)}
  .card--front{top:110px}
  .card--back{top:700px}

  /* front */
  .front-brand{position:absolute;left:0;right:0;top:130px;text-align:center;font-size:40px;font-weight:600;letter-spacing:12px;color:var(--muted)}
  .front-brand .brand-square{display:inline-block;width:14px;height:14px;background:var(--muted);margin-right:14px;vertical-align:middle}
  .front-web{position:absolute;left:40px;bottom:36px;display:flex;align-items:center;gap:14px;font-size:17px;color:var(--white)}
  .front-web .dash{width:50px;height:3px;background:var(--red)}

  /* back */
  .agent-photo{position:absolute;left:0;bottom:0;width:255px;height:270px;background:linear-gradient(180deg,var(--photo-b) 0%,var(--photo-b) 45%,var(--photo-a) 60%,var(--photo-a) 100%);border-top-right-radius:120px 110px}
  .footer-band{position:absolute;left:255px;right:0;bottom:0;height:52px;background:var(--red);display:flex;align-items:center;padding-left:40px;font-size:18px;color:var(--white)}
  .logo{position:absolute;left:290px;top:50px;display:flex;align-items:center;gap:12px}
  .logo-square{width:14px;height:14px;background:var(--white)}
  .logo-name{font-size:34px;font-weight:600;letter-spacing:6px;color:var(--white)}
  .logo-rule{position:absolute;left:290px;top:102px;width:300px;height:1px;background:#8a8a8c}
  .details{position:absolute;left:290px;top:118px}
  .agent-name{font-size:22px;font-weight:700;color:var(--white)}
  .agent-title{font-size:15px;color:var(--red);margin-bottom:10px}
  .address{font-size:15px;line-height:1.3;margin-bottom:8px}
  .contact{display:flex;align-items:center;gap:10px;font-size:15px;line-height:1.45}
  .contact svg{width:13px;height:13px;fill:var(--red);flex:none}
</style>
</head>
<body>

<section class="card card--front">
  <div class="front-brand"><span class="brand-square"></span>DUNMORE</div>
  <div class="front-web"><span class="dash"></span>www.dunmorerealty.com<span class="dash"></span></div>
</section>

<section class="card card--back">
  <div class="agent-photo" role="img" aria-label="Portrait photo of the agent in a blue suit"></div>
  <div class="logo"><span class="logo-square"></span><span class="logo-name">DUNMORE</span></div>
  <div class="logo-rule"></div>
  <div class="details">
    <div class="agent-name">Marisa Delgado</div>
    <div class="agent-title">Managing Director</div>
    <div class="address">418 Alder Ave #2207,<br>Brookfield, CO 80531</div>
    <div class="contact">
      <svg viewBox="0 0 16 16"><path d="M3 1h3l1.5 4-2 1.2a9 9 0 0 0 4.3 4.3L11 8.5l4 1.5v3a2 2 0 0 1-2 2A13 13 0 0 1 1 3a2 2 0 0 1 2-2z"/></svg>555.210.4476
    </div>
    <div class="contact">
      <svg viewBox="0 0 16 16"><path d="M4 0h8a1 1 0 0 1 1 1v14a1 1 0 0 1-1 1H4a1 1 0 0 1-1-1V1a1 1 0 0 1 1-1zm1 2v10h6V2z"/></svg>555-318-0962
    </div>
    <div class="contact">
      <svg viewBox="0 0 16 16"><path d="M0 3h16v10H0zm1.5 1.3V12h13V4.3L8 9z"/></svg>mdelgado@dunmorerealty.com
    </div>
  </div>
  <div class="footer-band">www.dunmorerealty.com</div>
</section>

</body>
</html>
```